New letter head for Air Conditioning business

We need a new professional letter head design to suit our new re-branded air conditioning business. Our new logo is attached

```html
<!DOCTYPE html>
<html lang="en">
<head>
<meta charset="utf-8">
<title>Norvane Letterhead</title>
<link href="https://fonts.googleapis.com/css2?family=Lato:wght@400;700;900&display=swap" rel="stylesheet">
<style>
  :root {
    --backdrop: #ececec;
    --paper: #ffffff;
    --ink: #3a3a3a;
    --ink-soft: #5a5a5a;
    --brand-dark: #2e2e30;
    --brand-green: #5bb87a;
  }
  * { box-sizing: border-box; margin: 0; padding: 0; }
  html, body { width: 1200px; height: 795px; overflow: hidden; }
  body {
    background: var(--backdrop);
    font-family: "Lato", sans-serif;
    color: var(--ink);
    position: relative;
  }
  .letterhead {
    position: absolute;
    left: 330px; top: 15px;
    width: 541px; height: 765px;
    background: var(--paper);
    box-shadow: 0 6px 22px rgba(0,0,0,0.12);
    overflow: hidden;
  }
  .brand {
    position: absolute; left: 48px; top: 52px;
    display: flex; align-items: center; gap: 10px;
  }
  .brand-mark { width: 14px; height: 14px; background: var(--brand-green); }
  .brand-name {
    font-weight: 900; font-size: 30px; letter-spacing: 3px;
    color: var(--brand-dark); text-transform: uppercase; line-height: 1;
  }
  .contact {
    position: absolute; right: 48px; top: 44px;
    font-size: 8px; line-height: 1.5; color: var(--ink-soft);
  }
  .contact-row { display: flex; align-items: center; gap: 4px; }
  .contact-row svg { width: 7px; height: 7px; flex: none; }
  .letter {
    position: absolute; left: 70px; top: 175px; width: 405px;
    font-size: 8px; line-height: 1.6; color: var(--ink-soft);
  }
  .letter-date { margin-bottom: 14px; }
  .recipient { margin-bottom: 18px; }
  .recipient strong { color: var(--ink); font-weight: 700; }
  .salutation { margin-bottom: 14px; }
  .letter p.body { margin-bottom: 14px; }
  .closing { margin-top: 34px; }
  .signature {
    display: block; width: 140px; height: 26px; margin-top: 6px;
    background: linear-gradient(90deg, rgba(58,58,58,0.12), rgba(58,58,58,0.04));
  }
  .footer-line {
    position: absolute; left: 0; bottom: 0; width: 420px; height: 7px;
    background: var(--brand-dark);
  }
  .footer-web {
    position: absolute; right: 0; bottom: 0; width: 121px; height: 20px;
    background: var(--brand-green); color: #fff;
    font-size: 8px; font-weight: 700;
    display: flex; align-items: center; justify-content: center;
  }
</style>
</head>
<body>
  <main class="letterhead">
    <header>
      <div class="brand">
        <span class="brand-mark"></span>
        <span class="brand-name">Norvane</span>
      </div>
      <address class="contact" style="font-style:normal">
        <div>Level 4, 18 Harlow Lane</div>
        <div>Westmere, Australia 2100</div>
        <div class="contact-row">
          <svg viewBox="0 0 10 10"><path d="M2 1 L4 1 L5 3.5 L3.8 4.5 Q5 6.5 6 6.8 L7 5.6 L9 6.6 L9 8.6 Q4 9.5 1 2.6 Z" fill="#5bb87a"/></svg>
          (+1) 555 010 2040
        </div>
        <div class="contact-row">
          <svg viewBox="0 0 10 10"><rect x="0.5" y="2" width="9" height="6" fill="#5bb87a"/><path d="M0.5 2 L5 5.5 L9.5 2" stroke="#fff" fill="none" stroke-width="0.8"/></svg>
          hello@norvaneclimate.com
        </div>
      </address>
    </header>

    <section class="letter">
      <div class="letter-date">01 January 2050</div>
      <div class="recipient">
        <strong>Company (Pvt) Ltd.</strong><br>
        PO Box 3355 Mainville St<br>
        Sample City Country 3355
      </div>
      <div class="salutation">Dear Laura Bennett,</div>
      <p class="body">Lorem ipsum dolor sit amet, consectetuer adipiscing elit, sed diam nonummy nibh euismod tincidunt ut laoreet dolore magna aliquam erat volutpat. Ut wisi enim ad minim veniam, quis nostrud exerci tation ullamcorper suscipit lobortis nisl ut aliquip ex ea commodo consequat. Duis dolore te feugait nulla facilisi. Nam liber tempor cum soluta nobis eleifend option congue nihil imperdiet doming id quod mazim placerat facer possim assum. Lorem ipsum dolor sit amet, consectetuer adipiscing elit, sed diam nonummy nibh euismod tincidunt ut laoreet dolore magna aliquam erat volutpat. Ut wisi enim ad minim veniam, quis nostrud exerci tation ullamcorper suscipit lobortis nisl ut aliquip ex ea commodo consequat.</p>
      <p class="body">Consectetuer adipiscing elit, sed diam nonummy nibh euismod tincidunt ut laoreet dolore magna aliquam erat volutpat. Ut wisi enim ad minim veniam, quis nostrud exerci tation ullamcorper suscipit lobortis nisl ut aliquip ex ea commodo consequat. Consectetuer adipiscing elit, sed diam nonummy nibh euismod tincidunt ut laoreet dolore magna aliquam erat volutpat. Ut wisi enim ad minim veniam, quis nostrud exerci tation ullamcorper suscipit lobortis nisl ut aliquip ex ea commodo consequat.</p>
      <p class="body">Consectetuer adipiscing elit, sed diam nonummy nibh euismod tincidunt ut laoreet dolore magna aliquam erat volutpat. Ut wisi enim ad minim veniam, quis nostrud exerci tation ullamcorper suscipit lobortis nisl ut aliquip ex ea commodo consequat. Consectetuer adipiscing elit, sed diam nonummy nibh euismod tincidunt ut laoreet dolore magna aliquam erat volutpat. Ut wisi enim ad minim veniam, quis nostrud exerci tation ullamcorper suscipit lobortis nisl ut aliquip ex ea commodo consequat.</p>
      <div class="closing">Sincerely Yours</div>
      <span class="signature" role="img" aria-label="Handwritten signature of the sender"></span>
    </section>

    <footer>
      <div class="footer-line"></div>
      <div class="footer-web">www.norvaneclimate.com</div>
    </footer>
  </main>
</body>
</html>
```